Business card design for my company.
I would like the card's background colour to be black. You can also see our web site to get an idea of our brand. https://www.tmwhomecrafting.com.au/
- Name
- Email

```html
<!DOCTYPE html>
<html lang="en">
<head>
<meta charset="utf-8">
<title>TMW Home Crafting – Business Card</title>
<link rel="stylesheet" href="https://fonts.googleapis.com/css2?family=Open+Sans:wght@400;600;700&display=swap">
<style>
  :root {
    --stage: #2b2b2b;
    --card: #262626;
    --card-deep: #1f1f1f;
    --gloss: #151515;
    --green: #1e9b45;
    --white: #f2f2f2;
    --text: #e4e4e4;
    --muted: #cfcfcf;
  }
  * { margin: 0; padding: 0; box-sizing: border-box; }
  html, body {
    width: 1200px; height: 852px; overflow: hidden;
    background: var(--stage);
    font-family: "Open Sans", Arial, sans-serif;
  }
  .stage {
    position: relative; width: 1200px; height: 852px;
    display: flex; align-items: center; justify-content: center; gap: 40px;
  }
  .card {
    position: relative; width: 520px; height: 300px;
    border-radius: 18px; overflow: hidden;
    background: linear-gradient(160deg, var(--card) 0%, var(--card-deep) 100%);
    box-shadow: 0 10px 24px rgba(0,0,0,.45);
  }
  /* Back side */
  .card-back .brand-name {
    position: absolute; left: 0; right: 0; top: 118px;
    text-align: center; font-weight: 700; font-size: 34px;
    letter-spacing: 3px; color: var(--gloss);
  }
  .card-back .website {
    position: absolute; right: 36px; bottom: 26px;
    font-size: 13px; color: var(--muted); letter-spacing: .3px;
  }
  /* Front side */
  .card-front .accent-lines { position: absolute; inset: 0; }
  .card-front .brand-name {
    position: absolute; right: 30px; top: 42px;
    font-weight: 700; font-size: 22px; letter-spacing: 2px; color: var(--white);
  }
  .person { position: absolute; left: 34px; top: 118px; }
  .person-name { font-size: 22px; font-weight: 600; color: var(--green); line-height: 1.1; }
  .person-role { font-size: 13px; color: var(--text); margin-top: 3px; }
  .contact-list { position: absolute; left: 34px; top: 196px; list-style: none; }
  .contact-list li {
    display: flex; align-items: center; gap: 10px;
    font-size: 13px; color: var(--text); line-height: 20px;
  }
  .contact-list svg { width: 12px; height: 12px; fill: var(--green); flex: none; }
</style>
</head>
<body>
<main class="stage">
  <section class="card card-back" aria-label="Card back">
    <div class="brand-name">TMW HOME CRAFTING</div>
    <div class="website">www.tmwhomecrafting.com.au</div>
  </section>

  <section class="card card-front" aria-label="Card front">
    <svg class="accent-lines" viewBox="0 0 520 300" aria-hidden="true">
      <polyline points="522,118 440,118 262,302" fill="none" stroke="var(--green)" stroke-width="5"/>
      <polyline points="522,140 452,140 300,302" fill="none" stroke="var(--green)" stroke-width="2"/>
    </svg>
    <div class="brand-name">TMW HOME CRAFTING</div>

    <div class="person">
      <div class="person-name">Liam Carver</div>
      <div class="person-role">General Manager</div>
    </div>

    <ul class="contact-list">
      <li>
        <svg viewBox="0 0 24 24"><path d="M6.6 10.8a15.1 15.1 0 0 0 6.6 6.6l2.2-2.2c.3-.3.7-.4 1-.2 1.1.4 2.3.6 3.6.6.6 0 1 .4 1 1V20c0 .6-.4 1-1 1A17 17 0 0 1 3 4c0-.6.4-1 1-1h3.5c.6 0 1 .4 1 1 0 1.3.2 2.5.6 3.6.1.3 0 .7-.2 1z"/></svg>
        0400 555 018
      </li>
      <li>
        <svg viewBox="0 0 24 24"><path d="M2 5h20v14H2zm2 2v.5l8 5 8-5V7zm0 2.8V17h16V9.8l-8 5z"/></svg>
        info@tmwhomecrafting.com.au
      </li>
      <li>
        <svg viewBox="0 0 24 24"><path d="M12 2a10 10 0 1 0 0 20 10 10 0 0 0 0-20zm6.9 9h-3a15 15 0 0 0-1.3-5.6A8 8 0 0 1 18.9 11zM12 4.1c.9 1.3 1.8 3.7 1.9 6.9h-3.8c.1-3.2 1-5.6 1.9-6.9zM9.4 5.4A15 15 0 0 0 8.1 11h-3a8 8 0 0 1 4.3-5.6zM5.1 13h3a15 15 0 0 0 1.3 5.6A8 8 0 0 1 5.1 13zm6.9 6.9c-.9-1.3-1.8-3.7-1.9-6.9h3.8c-.1 3.2-1 5.6-1.9 6.9zm2.6-1.3a15 15 0 0 0 1.3-5.6h3a8 8 0 0 1-4.3 5.6z"/></svg>
        www.tmwhomecrafting.com.au
      </li>
      <li>
        <svg viewBox="0 0 24 24"><path d="M12 2a7 7 0 0 0-7 7c0 5.2 7 13 7 13s7-7.8 7-13a7 7 0 0 0-7-7zm0 9.5A2.5 2.5 0 1 1 12 6.5a2.5 2.5 0 0 1 0 5z"/></svg>
        Kingston, Tasmania, Australia
      </li>
    </ul>
  </section>
</main>
</body>
</html>
```